Sea Shipping Logistics Company

The business is a logistics company (sea shipping and other special logistics) and also sales of bulk building materials.
The Design should be minimalistic and give a feeling of power and connectivity.
When the client sees the card, they should get a feeling of confident. Dark overall color (background) and print should be red / white .See logo. The card will be printed on trifecta with the middle color being red.

One side should be the logo and a 5 / 6 word slogan
And other side name, contact (phone/email) and a QR Code.

Target Market(s)

Construction companies / Oil & Gas related companies

Industry/Entity Type

Sea Bulk Shipping Logistics

Contact Information for Business Card

Name, Telephone number, Email address, Website URL, QR Code (see description)

Font styles to use
Sans Serif

Requirements
Must have
• No idea
Nice to have
• Minimalistic, but strong and powerful look and feel.

```html
<!DOCTYPE html>
<html lang="en">
<head>
<meta charset="utf-8">
<title>Korva Freight – Business Card</title>
<link href="https://fonts.googleapis.com/css2?family=Archivo:wght@900&family=Poppins:wght@400&family=Roboto:wght@400&display=swap" rel="stylesheet">
<style>
  :root {
    --stage: #221f1f;
    --brand-red: #cf0022;
    --card-white: #eeeef0;
    --ink: #141414;
    --steel: #3a3a3c;
    --tagline: #f3e6e8;
    --qr-field: #d9d9dc;
  }
  * { box-sizing: border-box; margin: 0; padding: 0; }
  html, body { width: 1200px; height: 1200px; overflow: hidden; }
  body { background: var(--stage); position: relative; font-family: "Roboto", sans-serif; }

  .card {
    position: absolute;
    width: 594px;
    height: 350px;
    border-radius: 24px;
    overflow: hidden;
  }

  /* Front */
  .card--front { left: 298px; top: 198px; background: var(--brand-red); }
  .front-brand {
    position: absolute; left: 0; right: 0; top: 134px;
    display: flex; align-items: center; justify-content: center; gap: 14px;
  }
  .front-brand__mark { width: 36px; height: 36px; background: var(--steel); }
  .front-brand__name {
    font-family: "Archivo", sans-serif; font-weight: 900;
    font-size: 42px; letter-spacing: -1px; color: var(--steel); line-height: 1;
  }
  .front-tagline {
    position: absolute; left: 0; right: 0; top: 296px;
    text-align: center;
    font-family: "Poppins", sans-serif; font-size: 15px; letter-spacing: 1.2px;
    color: var(--tagline);
  }
  .front-tagline .sep { margin: 0 12px; }

  /* Back */
  .card--back { left: 293px; top: 636px; background: var(--card-white); }
  .back-band { position: absolute; left: 0; top: 0; bottom: 0; width: 58px; background: var(--brand-red); }
  .back-rule { position: absolute; left: 61px; top: 0; bottom: 0; width: 4px; background: var(--ink); }

  .back-brand {
    position: absolute; left: 89px; top: 52px;
    display: flex; align-items: center; gap: 10px;
  }
  .back-brand__mark { width: 26px; height: 26px; background: var(--brand-red); }
  .back-brand__name {
    font-family: "Archivo", sans-serif; font-weight: 900;
    font-size: 32px; letter-spacing: -0.8px; color: var(--ink); line-height: 1;
  }

  .qr-code {
    position: absolute; left: 466px; top: 34px;
    width: 92px; height: 92px;
    background: var(--qr-field);
    border: 4px solid var(--ink);
  }

  .holder { position: absolute; left: 89px; top: 206px; }
  .holder__name {
    font-family: "Archivo", sans-serif; font-weight: 900;
    font-size: 25px; color: var(--brand-red); line-height: 1; letter-spacing: 0.3px;
  }
  .holder__role { font-size: 16px; color: var(--ink); margin-top: 4px; }

  .contact { position: absolute; top: 272px; list-style: none; }
  .contact--left { left: 89px; }
  .contact--right { left: 356px; top: 270px; }
  .contact li {
    display: flex; align-items: center; gap: 9px;
    font-size: 16px; color: var(--ink); height: 23px;
  }
  .contact svg { width: 15px; height: 15px; fill: var(--brand-red); flex: none; }
  .contact .accent { color: var(--brand-red); }
</style>
</head>
<body>

<section class="card card--front" aria-label="Card front">
  <div class="front-brand">
    <span class="front-brand__mark"></span>
    <span class="front-brand__name">KORVA FREIGHT</span>
  </div>
  <p class="front-tagline">SEA FREIGHT<span class="sep">|</span>BULK CARGO<span class="sep">|</span>LOGISTICS</p>
</section>

<section class="card card--back" aria-label="Card back">
  <div class="back-band"></div>
  <div class="back-rule"></div>

  <div class="back-brand">
    <span class="back-brand__mark"></span>
    <span class="back-brand__name">KORVA FREIGHT</span>
  </div>

  <div class="qr-code" role="img" aria-label="QR code linking to the company website"></div>

  <div class="holder">
    <h1 class="holder__name">DANIEL BROOKS</h1>
    <p class="holder__role">Managing Director</p>
  </div>

  <ul class="contact contact--left">
    <li>
      <svg viewBox="0 0 16 16" aria-hidden="true"><path d="M1 6c0-2 3-4 7-4s7 2 7 4v1h-3V5.5H4V7H1z"/><path d="M3 8h10l1 6H2z M6 10a2 2 0 1 0 4 0a2 2 0 1 0-4 0"/></svg>
      +597 555-0132
    </li>
    <li>
      <svg viewBox="0 0 16 16" aria-hidden="true"><path d="M8 0a5.5 5.5 0 0 0-5.5 5.5C2.5 10 8 16 8 16s5.5-6 5.5-10.5A5.5 5.5 0 0 0 8 0zm0 8a2.5 2.5 0 1 1 0-5a2.5 2.5 0 0 1 0 5z"/></svg>
      Havenweg 12, Paramaribo
    </li>
  </ul>

  <ul class="contact contact--right">
    <li>
      <svg viewBox="0 0 16 16" aria-hidden="true"><path d="M1 3h14v10H1z"/><path d="M1.5 3.8 8 9l6.5-5.2" fill="none" stroke="#eeeef0" stroke-width="1.4"/></svg>
      info@korva-freight.com
    </li>
    <li>
      <svg viewBox="0 0 16 16" aria-hidden="true"><circle cx="8" cy="8" r="6.5" fill="none" stroke="#cf0022" stroke-width="1.4"/><ellipse cx="8" cy="8" rx="2.8" ry="6.5" fill="none" stroke="#cf0022" stroke-width="1.2"/><path d="M1.5 8h13M2.5 4.8h11M2.5 11.2h11" stroke="#cf0022" stroke-width="1.1"/></svg>
      <span>www.<span class="accent">korva</span>-freight.com</span>
    </li>
  </ul>
</section>

</body>
</html>
```